Graphic Design Project

Enhance the look of our home page. Please note, we do not want a complete redesign. We just want to tweak it some to optimize a user's first impression. Dev-ready files not required - a mockup will be fine (jpg or pdf).

I have attached source file for our current page.

Specific objectives:

- We really like the modern look of "www.lo.zq" website. Would like to tighten up our appearance just a little to be more similar.

- A more creative design for the 4 text boxes in the middle of the page. Currently looks sub-par and outdated. We want a modern appearance.

- Colors can be revised some if you believe it will modernize / enhance the design.

Please submit your designs as soon as possible as we are under a huge time crunch and will be making our selections early.

The winner of this contest will get a followup project as well. We have a few upcoming tasks that will require a top-notch modern designer.

Industry/Entity Type

Graphic Design

Requirements
Must have
• - We really like the modern look of "www.lo.zq" website. Would like to tighten up our appearance just a little to be more similar.

- A more creative design for the 4 text boxes in the middle of the page. Currently looks sub-par and outdated.

- Colors can be revised some if you believe it will enhance the appearance.

```html
<!DOCTYPE html>
<html lang="en">
<head>
<meta charset="utf-8">
<title>LinkReach – Activate Profile</title>
<link href="https://fonts.googleapis.com/css2?family=Oswald:wght@400;500&family=Playfair+Display:ital@1&family=Open+Sans:wght@400;600;700&family=Arimo:wght@400;700&display=swap" rel="stylesheet">
<style>
:root{
  --ink:#111;
  --bar:#0d0d0d;
  --page:#e9e9e9;
  --ghost:#f6f6f6;
  --ghost-ring:#d8d8d8;
  --brand-blue:#4a9fe0;
  --nav-blue:#3b8fc0;
  --green-hi:#8fd43a;
  --green-lo:#4f9a12;
  --meter:#5aa3dc;
  --panel:#f2f2f2;
  --muted:#555;
}
*{box-sizing:border-box;margin:0;padding:0}
html,body{width:1200px;height:788px;overflow:hidden}
body{position:relative;background:radial-gradient(ellipse at 45% 45%,#f7f7f7 0%,var(--page) 70%,#dcdcdc 100%);font-family:"Open Sans",Arial,sans-serif;color:var(--ink)}
.abs{position:absolute}

/* header */
.site-header{position:absolute;left:0;top:0;width:1200px;height:46px;background:linear-gradient(#2a2a2a,#050505);box-shadow:0 2px 6px rgba(0,0,0,.4)}
.brand{left:225px;top:6px;color:#fff}
.brand-name{font:700 22px/1 "Open Sans",sans-serif;color:var(--brand-blue);display:flex;align-items:center;gap:6px}
.brand-name i{display:inline-block;width:12px;height:12px;border-radius:50%;background:var(--brand-blue)}
.brand-tag{font-size:9.5px;color:#ddd;margin-top:2px}
.nav-link{left:597px;top:17px;font:700 10px "Open Sans",sans-serif;color:#fff}
.nav-link span{font-weight:400}
.nav-btn{top:13px;height:22px;border-radius:3px;font:600 7.5px/22px "Open Sans",sans-serif;text-align:center;text-transform:uppercase}
.nav-btn.light{left:722px;width:117px;background:linear-gradient(#f4f4f4,#c9c9c9);color:#3a7cb0}
.nav-btn.blue{left:858px;width:117px;background:linear-gradient(#4aa6d6,#2a77a6);color:#fff}
.nav-sep{left:848px;top:12px;width:1px;height:24px;background:#555}

/* faint background stats */
.ghost{font-family:Arimo,Arial,sans-serif;font-weight:700;color:var(--ghost);letter-spacing:1px}
.ghost-ring{border-radius:50%;border:2px solid var(--ghost)}

/* hero */
.hero-title{right:724px;top:165px;font:500 33px/1 Oswald,sans-serif;color:#1a1a1a;letter-spacing:.5px}
.hero-sub{right:724px;top:204px;font:italic 24px "Playfair Display",serif;color:#222}
.signin{left:312px;top:243px;width:164px;height:62px;border-radius:8px;background:linear-gradient(var(--green-hi),var(--green-lo));box-shadow:0 5px 6px rgba(0,0,0,.25);color:#fff;font:500 16px "Open Sans",sans-serif;display:flex;align-items:center;padding-left:57px}
.signin i{position:absolute;right:9px;top:14px;width:34px;height:34px;border-radius:50%;background:#3f8a0d}

.portrait{left:700px;top:62px;width:360px;height:690px;border-radius:170px 170px 0 0;background:linear-gradient(#9a6a45 0%,#c79a7e 22%,#d9b8a0 33%,#2a2f45 45%,#1d2235 100%)}

/* compare panel */
.compare{left:225px;top:379px;width:283px;height:218px;background:#000;color:#fff}
.compare-head{left:28px;top:35px;font:500 14px Oswald,sans-serif;display:flex;align-items:center;gap:6px}
.compare-frame{left:188px;top:44px;width:81px;height:135px;border:1px solid #444;border-left:none}
.compare-rule{left:118px;top:44px;width:150px;height:1px;background:#444}
.compare-text{left:34px;top:81px;width:230px;font:20px/23px Arimo,Arial,sans-serif}
.dots{left:190px;top:191px;display:flex;gap:11px}
.dots i{width:10px;height:10px;border-radius:50%;background:var(--brand-blue)}
.dots i:first-child{background:#fff}

.profile{left:508px;top:379px;width:467px;height:218px;background:linear-gradient(90deg,#fafafa,#eee);box-shadow:0 4px 10px rgba(0,0,0,.25)}
.avatar{left:23px;top:1px;width:62px;height:78px;background:linear-gradient(#c9c2b6,#55606c);border:3px solid #fff}
.stars{left:24px;top:85px;display:flex;gap:1px}
.stars i{width:11px;height:11px;border:1px solid #bbb;border-radius:2px;background:#eee}
.meta{left:0;font-size:9.5px;color:#333}
.meta b{font-weight:700}
.help{display:inline-block;width:10px;height:10px;border-radius:50%;background:#3c86c6;color:#fff;font-size:7px;text-align:center;line-height:10px;vertical-align:middle}
.name-bar{left:137px;top:-3px;width:306px;height:24px;background:linear-gradient(#8e8e8e,#6d6d6d);color:#eee;font:15px/24px Oswald,sans-serif;text-align:center}
.stats-head{left:137px;top:28px;width:306px;height:40px;background:#e2e2e2}
.rank{left:117px;top:110px;width:36px;height:36px;border-radius:50%;border:1px solid #999;background:#fff;font:700 8px "Open Sans",sans-serif;text-align:center;padding-top:6px}
.col{top:32px;width:60px;text-align:center}
.col .sq{display:block;margin:0 auto;width:18px;height:18px;border-radius:3px;background:var(--brand-blue)}
.col .num{font:700 10px Arimo,Arial,sans-serif;margin-top:2px;display:block}
.meter{top:77px;width:12px;height:104px;border-radius:3px;background:var(--meter);box-shadow:inset 0 0 0 1px #3f85c0}
.meter-lbl{top:78px;font-size:7.5px;color:#333;line-height:1}
.meter-val{font:700 7px Arimo,sans-serif;color:#fff}
.col-foot{top:189px;width:306px;left:137px;height:20px;background:#dedede}
.col-link{top:194px;font-size:8px;text-decoration:underline;color:#333}

/* footer */
.follow{top:724px;height:28px;background:#2b2b2b;border-radius:4px 4px 0 0;color:#fff;font:600 9.5px/28px "Open Sans",sans-serif;padding:0 10px 0 28px}
.follow i{position:absolute;left:8px;top:8px;width:12px;height:12px;border-radius:2px;background:#fff}
.site-footer{left:0;top:752px;width:1200px;height:36px;background:var(--bar);color:#fff}
.copy{left:226px;top:13px;font-size:8.5px}
.social{left:476px;top:10px;display:flex;gap:8px}
.social i{width:16px;height:16px;border-radius:50%;background:#ddd}
.foot-links{left:585px;top:0;display:flex;height:36px}
.foot-links a{color:#fff;text-decoration:none;font-size:12px;line-height:36px;padding:0 13px;border-left:1px solid #444}
.foot-links a:first-child{border-left:none}
</style>
</head>
<body>

<div class="abs ghost" style="left:395px;top:62px;font-size:82px">2,815</div>
<div class="abs ghost" style="left:622px;top:74px;font-size:38px">friends</div>
<div class="abs ghost-ring" style="left:318px;top:67px;width:58px;height:58px"></div>
<div class="abs ghost" style="left:68px;top:302px;font-size:60px">38,502</div>
<div class="abs ghost" style="left:286px;top:308px;font-size:30px">followers</div>
<div class="abs ghost-ring" style="left:0;top:305px;width:48px;height:48px"></div>
<div class="abs ghost" style="left:85px;top:535px;font-size:48px">STRE</div>
<div class="abs ghost" style="left:450px;top:625px;font-size:72px">924</div>
<div class="abs ghost" style="left:592px;top:632px;font-size:34px">contacts</div>
<div class="abs ghost-ring" style="left:360px;top:628px;width:62px;height:62px"></div>
<div class="abs" style="left:520px;top:150px;width:260px;height:260px;border-radius:50%;border:34px solid #dcdcdc"></div>
<div class="abs ghost" style="left:595px;top:262px;font-size:25px;color:#d4d4d4;line-height:25px">TOP<br>INDUSTRY</div>
<div class="abs" style="left:128px;top:615px;width:170px;height:170px;border-radius:50%;border:24px solid #d4d4d4"></div>
<div class="abs ghost" style="left:180px;top:685px;font-size:42px;color:#d0d0d0">22<sup style="font-size:20px">%</sup></div>
<svg class="abs" style="left:0;top:0" width="1200" height="788" aria-hidden="true">
  <g stroke="#f4f4f4" stroke-width="2" fill="none">
    <path d="M24 330 L330 100 M24 330 L200 560 M200 560 L391 660 M391 660 L560 620"/>
  </g>
</svg>

<header class="site-header">
  <div class="abs brand">
    <div class="brand-name"><i></i>LinkReach</div>
    <div class="brand-tag">The Source of Networking Superstars</div>
  </div>
  <div class="abs nav-link">SIGN IN <span>or</span> LEARN MORE</div>
  <div class="abs nav-btn light">Networking Superstars</div>
  <div class="abs nav-sep"></div>
  <div class="abs nav-btn blue">Business Users/Recruiters</div>
</header>

<div class="abs portrait" role="img" aria-label="Photo of a smiling businesswoman in a pinstripe suit pointing toward the sign-in button"></div>

<h1 class="abs hero-title">ACTIVATE PROFILE</h1>
<p class="abs hero-sub">Instantly With Chirper</p>
<div class="abs signin">Sign In<i></i></div>

<section class="abs compare">
  <div class="abs compare-head">
    <svg width="18" height="12" viewBox="0 0 18 12" aria-hidden="true"><path d="M2 5V2h10l-2-2M16 7v3H6l2 2" stroke="#fff" stroke-width="2" fill="none"/></svg>COMPARE
  </div>
  <div class="abs compare-rule"></div>
  <div class="abs compare-frame"></div>
  <p class="abs compare-text">against others within our databse to see how you rank</p>
  <div class="abs dots"><i></i><i></i><i></i><i></i></div>
</section>

<section class="abs profile">
  <div class="abs avatar" role="img" aria-label="Profile photo of a member holding a sign"></div>
  <div class="abs stars"><i></i><i></i><i></i><i></i><i></i></div>
  <div class="abs meta" style="top:113px"><b>Location:</b></div>
  <div class="abs meta" style="top:126px">Riverton, AZ</div>
  <div class="abs meta" style="top:154px"><b>Position:</b> <span class="help">?</span></div>
  <div class="abs meta" style="top:168px">Full time</div>
  <div class="abs meta" style="top:184px">Part time</div>
  <div class="abs meta" style="top:200px">Promotional</div>

  <div class="abs name-bar">Sam Sample</div>
  <div class="abs stats-head"></div>
  <div class="abs rank">Rank<br><span class="help">?</span></div>

  <div class="abs col" style="left:148px"><span class="sq"></span><span class="num">36,452</span></div>
  <div class="abs col" style="left:222px"><span class="sq"></span><span class="num">36,452</span></div>
  <div class="abs col" style="left:298px"><span class="sq"></span><span class="num">36,452</span></div>
  <div class="abs col" style="left:373px"><span class="sq" style="background:#e8e8e8;border:1px solid #555"></span><span class="num">36,452</span></div>

  <div class="abs meter" style="left:159px"><span class="abs meter-val" style="left:1px;top:17px">50</span></div>
  <div class="abs meter" style="left:235px"><span class="abs meter-val" style="left:1px;top:50px">50</span></div>
  <div class="abs meter" style="left:312px"><span class="abs meter-val" style="left:1px;top:78px">20</span></div>
  <div class="abs meter" style="left:388px"><span class="abs meter-val" style="left:1px;top:24px">70</span></div>

  <div class="abs meter-lbl" style="left:173px">-100%<br><br><br><br><br>-<br><br><br><br><br><br>-0%</div>
  <div class="abs meter-lbl" style="left:249px">-100%<br><br><br><br><br>-<br><br><br><br><br><br>-0%</div>
  <div class="abs meter-lbl" style="left:326px">-100%<br><br><br><br><br>-<br><br><br><br><br><br>-0%</div>
  <div class="abs meter-lbl" style="left:402px">-100%<br><br><br><br><br>-<br><br><br><br><br><br>-0%</div>

  <div class="abs col-foot"></div>
  <div class="abs col-link" style="left:159px">FOLLOW</div>
  <div class="abs col-link" style="left:239px">FRIEND</div>
  <div class="abs col-link" style="left:311px">CONNECT</div>
</section>

<div class="abs follow" style="left:225px"><i></i>Follow us on Chirper</div>
<div class="abs follow" style="left:372px"><i></i>Follow us on Facepage</div>

<footer class="abs site-footer">
  <div class="abs copy">Copyright © 2013 LinkReach. All rights reserved.</div>
  <div class="abs social"><i></i><i></i><i></i><i></i></div>
  <nav class="abs foot-links">
    <a href="#">Contact Us</a><a href="#">Sample Profile</a><a href="#">Terms of Services</a><a href="#">Privacy Policy</a>
  </nav>
</footer>

</body>
</html>
```